Visitenkarten-Design für virtuelle Jobmesse & Jobbörse für Soldaten
Zielgruppe
Die KVL GmbH ist ein Unternehmen das zwei Hauptprodukte betreibt! Zum einen Jobbörse für Soldaten unter www.laufbahnwechsel-beispiel.de und zum anderen eine virtuelle Jobmesse für Soldaten unter www.merivon-beispiel.de , die wir zweimal im Jahr veranstalten.
Aufgabenstellung
Wir haben ja die beiden Produkte Laufbahnwechsel.de und die Merivon, für die bereits jeweils ein separtes Logo besteht! Diese finden Sie im Anhang! Beide werden doch jedoch von einem Unternehmen, der KVL GmbH betrieben! Aktuell nutzen wir eine Visitenkarte mit dem Logo von KVL und eine mit dem Logo der MERIVON. Gerade im Hinblick darauf, dass wir zukünftig auch weiter Plattformen in unser Portfolio aufnehmen, möchte ich hier unsere V-Karten flexibler gestalten!
Ziel soll es also sein, eine Visitenkarte zu gestalten, auf dem klar wird, dass der Mitarbeiter von der KVL GmbH kommt, die KVL GmbH aber unterschiedliche Produkte betreibt.
Im Anhang finden Sie:
1. Das Logo von KVL
2. Das Logo von Merivon
3. Die aktuelle V-Karte von KVL
4. Die aktuelle V-Karte von MERIVON
Vielleicht ein kleiner Anreiz: Aktuell nutzen wir auch zwei getrennte Geschäftspapiere. Das von www.laufbahnwechsel-beispiel.de lade ich einmal hoch! Der Designer, der auch die Visitenkarte erstellt, erhällt im Anschluss den 1:1 Auftrag in Höhe von 200 Euro für die Erstellung des Geschäftspapiers! Wenn Sie jetzt schon einen Vorschlag für das Geschäftspapier einreichen, erhöht das natürlich Ihre Chancen, wobei ich verspreche, dass wir im Falle eine Annahme das 1:1 im Anschluß dennoch starten werden!

```html
<!DOCTYPE html>
<html lang="de">
<head>
<meta charset="utf-8">
<title>Visitenkarte KVL GmbH</title>
<link href="https://fonts.googleapis.com/css2?family=Arimo:wght@400;700&display=swap" rel="stylesheet">
<style>
  :root {
    --bg: #b9c0c4;
    --card: #f1f1f1;
    --blue: #1d4178;
    --grey-line: #8a8a8a;
    --green: #3b5e2b;
    --text: #3a3a3a;
    --white: #ffffff;
  }
  * { margin: 0; padding: 0; box-sizing: border-box; }
  html, body { width: 1200px; height: 900px; overflow: hidden; }
  body {
    background: var(--bg);
    font-family: "Arimo", Arial, sans-serif;
    position: relative;
  }
  .card {
    position: absolute;
    top: 275px;
    width: 540px;
    height: 350px;
    background: var(--card);
    box-shadow: 0 6px 18px rgba(0,0,0,.18);
    overflow: hidden;
  }
  .card--back { left: 40px; }
  .card--front { left: 620px; }

  .rule {
    position: absolute;
    left: 0;
    right: 0;
    height: 5px;
    border-top: 2px solid var(--blue);
    border-bottom: 1px solid var(--grey-line);
  }
  .card--back .rule { top: 173px; }
  .card--front .rule { top: 62px; }

  .brand-mark {
    position: absolute;
    background: var(--card);
    color: var(--blue);
    font-weight: 700;
    white-space: nowrap;
  }
  .card--back .brand-mark {
    left: 50%;
    top: 175px;
    transform: translate(-50%, -50%);
    font-size: 36px;
    padding: 0 22px;
  }
  .card--front .brand-mark {
    right: 30px;
    top: 50px;
    font-size: 20px;
    padding: 0 12px;
  }

  .holder {
    position: absolute;
    left: 40px;
    top: 158px;
  }
  .holder__name { color: var(--blue); font-weight: 700; font-size: 23px; }
  .holder__role { color: var(--text); font-size: 13px; margin-top: 3px; }

  .company {
    position: absolute;
    right: 30px;
    top: 84px;
    text-align: right;
  }
  .company__name { color: var(--text); font-weight: 700; font-size: 22px; }
  .product {
    margin-top: 6px;
    display: flex;
    justify-content: flex-end;
    align-items: center;
    gap: 6px;
    color: var(--green);
    font-weight: 700;
    font-size: 11px;
    letter-spacing: 1px;
  }
  .product__dot { width: 9px; height: 9px; border-radius: 50%; background: var(--green); }
  .product__site { color: var(--green); font-weight: 700; font-size: 15px; margin-top: 4px; }
  .product__note { color: var(--green); font-weight: 700; font-size: 10px; margin-top: 2px; }

  .contact {
    position: absolute;
    right: 30px;
    top: 222px;
    text-align: right;
    color: var(--text);
    font-size: 11.5px;
    line-height: 1.5;
  }

  .url-band {
    position: absolute;
    left: 0;
    right: 0;
    bottom: 0;
    height: 40px;
    background: linear-gradient(90deg, var(--green) 0%, var(--green) 35%, var(--blue) 100%);
    display: flex;
    justify-content: space-between;
    align-items: center;
    padding: 0 24px;
    color: var(--white);
    font-weight: 700;
    font-size: 14px;
  }
</style>
</head>
<body>

  <section class="card card--back" aria-label="Rückseite">
    <div class="rule"></div>
    <div class="brand-mark">Laufbahnwechsel</div>
  </section>

  <section class="card card--front" aria-label="Vorderseite">
    <div class="rule"></div>
    <div class="brand-mark">Laufbahnwechsel</div>

    <div class="company">
      <div class="company__name">KVL GmbH</div>
      <div class="product"><span class="product__dot"></span>MERIVON</div>
      <div class="product__site">Merivon.de</div>
      <div class="product__note">ist eine Marke der KVL GmbH</div>
    </div>

    <div class="holder">
      <div class="holder__name">Jonas Berger</div>
      <div class="holder__role">Geschäftsführer</div>
    </div>

    <div class="contact">
      Lindenweg 14 • 12345 Musterstadt<br>
      Telefon: 01234 - 567 89 10 • Mobil: 0170 - 123 45 678<br>
      jonas.berger@merivon-beispiel.de • jonas.berger@laufbahnwechsel-beispiel.de
    </div>

    <div class="url-band">
      <span>www.merivon-beispiel.de</span>
      <span>www.laufbahnwechsel-beispiel.de</span>
    </div>
  </section>

</body>
</html>
```